Animal Eye Clinic needs a Business card

We are a new veterinary ophthalmology practice (Ridgeline Pet Vision Care) and we need a business card designed. We only see animal eyes - we are not a regular veterinary clinic. We already have a logo. We are looking for a professional, good looking business card to hand out to our clients. We are looking for something simple but professional and contemporary. Our logo is likely the only picture/graphic that needs to be on the card.
Updates

Contact Information for Business Card

Delia Vossman, BSc, DVM, MSc, DipACVO
Veterinary Ophthalmologist

Phone: 250.418.3927
Email: ridgelinepetvisioncare@mailbox-example.net
Website: ridgelinepetvisioncare-example.net
Address: 1874 Thornbury Rd
Alderbrook, NS, V1X 4M9

Colors

Designer to choose colors to be used in the design.

Requirements
Must have
• Our logo (attached)

```html
<!DOCTYPE html>
<html lang="en">
<head>
<meta charset="utf-8">
<title>Ridgeline Pet Vision Care – Business Card</title>
<link rel="stylesheet" href="https://fonts.googleapis.com/css2?family=Roboto:wght@400;500;700&display=swap">
<style>
  :root {
    --page-bg: #e4e2df;
    --card-light: #f3f4f4;
    --card-mid: #dfe3e4;
    --teal: #1e6a73;
    --teal-dark: #0f4f57;
    --teal-light: #2a8089;
    --charcoal: #3b3838;
    --charcoal-dark: #2c2a2a;
    --text-light: #eef0f0;
    --text-soft: #d9dfe0;
    --rule: #d8d2cc;
  }
  * { box-sizing: border-box; margin: 0; padding: 0; }
  html, body {
    width: 1200px; height: 970px; overflow: hidden;
    background: var(--page-bg);
    font-family: "Roboto", Arial, sans-serif;
  }
  .card {
    position: absolute; left: 80px; top: 188px;
    width: 1040px; height: 594px;
    background: linear-gradient(160deg, var(--card-light) 0%, #fafbfb 45%, var(--card-mid) 100%);
    box-shadow: 0 18px 40px rgba(0,0,0,0.18);
    overflow: hidden;
  }
  .brand {
    position: absolute; left: 58px; top: 76px;
    display: flex; align-items: center; gap: 40px;
  }
  .brand-dot {
    width: 150px; height: 150px; border-radius: 50%;
    background: var(--teal);
    flex: none;
  }
  .brand-name {
    color: var(--teal);
    font-weight: 700; font-size: 48px; line-height: 1.08;
    text-transform: uppercase; letter-spacing: 0.5px;
  }
  .name-band {
    position: absolute; left: 0; top: 308px;
    width: 725px; height: 86px;
    background: linear-gradient(90deg, var(--charcoal-dark), var(--charcoal) 70%, #474343);
    border-bottom: 3px solid var(--rule);
    padding: 10px 0 0 56px;
  }
  .person-name { color: var(--text-light); font-size: 30px; font-weight: 500; line-height: 36px; }
  .person-title { color: var(--text-soft); font-size: 23px; line-height: 28px; margin-top: 2px; }
  .contact-band {
    position: absolute; left: 0; top: 397px;
    width: 100%; height: 197px;
    background: linear-gradient(180deg, var(--teal-light), var(--teal) 40%, var(--teal-dark));
    padding: 18px 0 0 56px;
    color: var(--text-soft);
    font-size: 23px;
  }
  .address p { line-height: 33px; }
  .contact-list { list-style: none; margin-top: 16px; }
  .contact-list li { display: flex; align-items: center; gap: 10px; line-height: 34px; }
  .contact-icon { width: 26px; height: 26px; flex: none; }
</style>
</head>
<body>
  <div class="card">
    <div class="brand">
      <div class="brand-dot"></div>
      <div class="brand-name">Ridgeline<br>Pet Vision Care</div>
    </div>

    <div class="name-band">
      <div class="person-name">Delia Vossman, BSc, DVM, MSc, DipACVO</div>
      <div class="person-title">Veterinary Ophthalmologist</div>
    </div>

    <div class="contact-band">
      <div class="address">
        <p>1874 Thornbury Rd</p>
        <p>Alderbrook, NS, V1X 4M9</p>
      </div>
      <ul class="contact-list">
        <li>
          <svg class="contact-icon" viewBox="0 0 26 26" aria-hidden="true">
            <circle cx="13" cy="13" r="13" fill="#d9dfe0"/>
            <path d="M9 6.5c.8-.4 1.6 0 2 .8l1 2.2c.3.7.1 1.4-.5 1.8l-.9.6c.7 1.6 2 2.9 3.6 3.6l.6-.9c.4-.6 1.1-.8 1.8-.5l2.2 1c.8.4 1.2 1.2.8 2-.6 1.4-2 2.2-3.5 1.9-4.2-.9-7.4-4.1-8.3-8.3-.3-1.5.5-2.9 1.9-3.5z" fill="#1e6a73"/>
          </svg>
          250.418.3927
        </li>
        <li>
          <svg class="contact-icon" viewBox="0 0 26 26" aria-hidden="true">
            <circle cx="13" cy="13" r="13" fill="#d9dfe0"/>
            <rect x="6.5" y="8.5" width="13" height="9" rx="1" fill="#1e6a73"/>
            <path d="M7 9l6 5 6-5" fill="none" stroke="#d9dfe0" stroke-width="1.3"/>
          </svg>
          ridgelinepetvisioncare@mailbox-example.net
        </li>
      </ul>
    </div>
  </div>
</body>
</html>
```